Update our OBGYN business card look and info

We are an OBGYN office. Our logo is nice but would like to "woman" part of the logo to be a darker color, to contrast with the flower that surrounds it. Maybe make our practice name Bloom Harbor Health more feminine. Our practice caters to women only. All providers and staff are female.

Target Market(s)

Females 16-65.

Industry/Entity Type

Business

Contact Information for Business Card

See attached upload. The ONLY CHANGE to the information is DELETE the name Paula Renwick, Midwife and REPLACE with Dora Fintelli, Midwife

Logo Text

Bloom Harbor Health Obstetrics & Gynecology

Font styles to use
Serif
Script

Colors
85cae6
0692cd
33a6d7
85abd2
f59195
eea4c8
cadf82
fac994
d3a5cc

```html
<!DOCTYPE html>
<html lang="en">
<head>
<meta charset="utf-8">
<title>Bloom Harbor Health – Business Card</title>
<link rel="stylesheet" href="https://fonts.googleapis.com/css2?family=Marcellus&family=Questrial&family=Arimo:wght@400;700&display=swap">
<style>
  :root {
    --bg: #2a2a2c;
    --card-white: #f4f5f5;
    --blue-light: #85cae6;
    --blue-front-a: #79bccf;
    --blue-front-b: #a3d4e1;
    --blue-name: #4fa9c9;
    --band-blue: #6fb8cc;
    --grey-text: #6b6c6f;
    --ink: #2f3033;
    --band-grey: #7b7c80;
    --band-grey-dark: #5c5d61;
  }
  * { box-sizing: border-box; margin: 0; padding: 0; }
  html, body { width: 1200px; height: 800px; overflow: hidden; }
  body { background: var(--bg); position: relative; font-family: "Arimo", sans-serif; }

  .card {
    position: absolute;
    width: 600px;
    height: 343px;
    box-shadow: 0 10px 30px rgba(0,0,0,.5);
    overflow: hidden;
  }

  /* Front side */
  .card--front {
    left: 520px; top: 40px;
    background: linear-gradient(135deg, var(--blue-front-a), var(--blue-front-b));
    color: #fff;
  }
  .card--front .faint-mark {
    position: absolute; right: -70px; top: 20px;
    width: 300px; height: 300px; border-radius: 50%;
    background: rgba(255,255,255,.12);
  }
  .card--front .brand {
    position: absolute; left: 120px; top: 108px;
    display: flex; align-items: center; gap: 18px;
  }
  .brand-dot { width: 56px; height: 56px; border-radius: 50%; background: #fff; flex: none; }
  .brand-dot--blue { background: var(--blue-light); width: 50px; height: 50px; }
  .brand-name {
    font-family: "Marcellus", serif; font-size: 22px; letter-spacing: .5px;
    text-transform: uppercase; line-height: 1.1;
  }
  .brand-sub { font-family: "Questrial", sans-serif; font-size: 21px; line-height: 1.2; }
  .card--front .web {
    position: absolute; left: 0; right: 0; bottom: 52px; text-align: center;
    font-family: "Questrial", sans-serif; font-size: 14px; letter-spacing: 3px;
  }

  /* Back side */
  .card--back {
    left: 80px; top: 410px;
    background: var(--card-white);
    color: var(--ink);
  }
  .card--back .brand {
    position: absolute; left: 34px; top: 26px;
    display: flex; align-items: center; gap: 16px;
  }
  .card--back .brand-name { color: var(--blue-name); font-size: 19px; }
  .card--back .brand-sub { color: var(--grey-text); font-size: 19px; }

  .address { position: absolute; left: 40px; top: 104px; font-size: 14px; line-height: 17px; }
  .divider { position: absolute; left: 40px; top: 164px; width: 36px; height: 2px; background: var(--blue-light); }
  .contacts { position: absolute; left: 40px; top: 178px; list-style: none; font-size: 14px; line-height: 18px; }
  .contacts li { display: flex; align-items: center; gap: 8px; }
  .contacts svg { width: 12px; height: 12px; flex: none; }

  .providers {
    position: absolute; right: 40px; top: 196px; text-align: right;
    font-size: 15px; line-height: 18px; list-style: none;
  }
  .providers b { font-weight: 700; }

  .bands { position: absolute; left: 0; bottom: 0; width: 600px; height: 60px; }
</style>
</head>
<body>

<section class="card card--front" aria-label="Card front">
  <div class="faint-mark"></div>
  <div class="brand">
    <span class="brand-dot"></span>
    <div>
      <div class="brand-name">Bloom Harbor Health</div>
      <div class="brand-sub">Obstetrics &amp; Gynecology</div>
    </div>
  </div>
  <div class="web">www.bloomharborhealth.com</div>
</section>

<section class="card card--back" aria-label="Card back">
  <div class="brand">
    <span class="brand-dot brand-dot--blue"></span>
    <div>
      <div class="brand-name">Bloom Harbor Health</div>
      <div class="brand-sub">Obstetrics &amp; Gynecology</div>
    </div>
  </div>

  <address class="address" style="font-style:normal">
    418 Linden Avenue<br>Suite 3B<br>Fairhaven, GA 31999
  </address>
  <div class="divider"></div>

  <ul class="contacts">
    <li><svg viewBox="0 0 12 12"><path d="M3 1l2 2.5-1.2 1.2a7 7 0 0 0 3.5 3.5L8.5 7 11 9l-1.5 2C5 11 1 7 1 2.5z" fill="none" stroke="#85cae6" stroke-width="1.1"/></svg>(555) 214-0387</li>
    <li><svg viewBox="0 0 12 12"><rect x="3" y="1" width="6" height="3" fill="none" stroke="#85cae6"/><rect x="1" y="4" width="10" height="5" fill="#85cae6"/><rect x="3" y="8" width="6" height="3" fill="#fff" stroke="#85cae6"/></svg>(555) 214-0392</li>
    <li><svg viewBox="0 0 12 12"><rect x="1" y="2.5" width="10" height="7" fill="none" stroke="#85cae6"/><path d="M1 2.5l5 4 5-4" fill="none" stroke="#85cae6"/></svg>info@bloomharborhealth.com</li>
    <li><svg viewBox="0 0 12 12"><circle cx="6" cy="6" r="5" fill="none" stroke="#85cae6"/><ellipse cx="6" cy="6" rx="2.2" ry="5" fill="none" stroke="#85cae6"/><path d="M1 6h10" stroke="#85cae6"/></svg>www.bloomharborhealth.com</li>
  </ul>

  <ul class="providers">
    <li><b>Helena Marsh,</b> MD</li>
    <li><b>Nadia Crowell,</b> MD</li>
    <li><b>Irene Solberg,</b> MD</li>
    <li><b>Dora Fintelli,</b> Midwife</li>
    <li><b>Tessa Whitford,</b> Midwife</li>
  </ul>

  <svg class="bands" viewBox="0 0 600 60" preserveAspectRatio="none" aria-hidden="true">
    <polygon points="0,0 250,0 250,38 600,38 600,60 0,60" fill="var(--band-grey)"/>
    <polygon points="250,8 280,0 280,38 250,38" fill="var(--band-grey-dark)"/>
    <polygon points="320,10 345,0 600,0 600,38 320,38" fill="var(--band-blue)"/>
    <rect x="0" y="52" width="600" height="8" fill="var(--band-grey-dark)"/>
  </svg>
</section>

</body>
</html>
```